Realty Group Needs Classy, Contemporary Letterhead Design

We need a letterhead design for a new realty company located in NY, USA. We buy investment properties to rehabilitate and or keep in our rental portfolio.

```html
<!DOCTYPE html>
<html lang="en">
<head>
<meta charset="utf-8">
<title>Meridian Realty Group — Letterhead</title>
<link href="https://fonts.googleapis.com/css2?family=Open+Sans:wght@400;600;700;800&display=swap" rel="stylesheet">
<style>
  :root {
    --backdrop: #e9e9ea;
    --paper: #ffffff;
    --brand-purple: #4a2a90;
    --rule-grey: #6d6d70;
    --ink: #2b2b2e;
    --ink-soft: #6a6a6e;
  }
  * { box-sizing: border-box; margin: 0; padding: 0; }
  html, body {
    width: 1200px; height: 795px; overflow: hidden;
    background: var(--backdrop);
    font-family: "Open Sans", Arial, sans-serif;
  }
  .letterhead {
    position: absolute; left: 333px; top: 20px;
    width: 534px; height: 755px;
    background: var(--paper);
    box-shadow: 0 2px 10px rgba(0,0,0,0.12);
    color: var(--ink);
  }
  .brand {
    position: absolute; left: 44px; top: 52px;
    display: flex; align-items: center; gap: 7px;
  }
  .brand-dot { width: 12px; height: 12px; border-radius: 50%; background: var(--brand-purple); }
  .brand-name {
    font-weight: 800; font-size: 19px; letter-spacing: 0.5px;
    color: var(--brand-purple); line-height: 1;
  }
  .brand-sub {
    position: absolute; left: 63px; top: 74px;
    font-size: 7px; font-weight: 600; letter-spacing: 1.5px; color: var(--brand-purple);
  }
  .contact {
    position: absolute; right: 44px; top: 48px;
    list-style: none; font-size: 7.5px; font-weight: 600; line-height: 12px;
  }
  .contact li { display: flex; align-items: center; gap: 5px; white-space: nowrap; }
  .contact svg { width: 9px; height: 9px; flex: none; }
  .letter {
    position: absolute; left: 60px; top: 165px; width: 414px;
    font-size: 9px; line-height: 13px; color: var(--ink-soft);
  }
  .date, .recipient { color: var(--ink); font-size: 9.5px; }
  .date { margin-bottom: 10px; }
  .recipient { line-height: 12.5px; margin-bottom: 12px; }
  .salutation { color: var(--ink); font-weight: 700; font-size: 10px; margin-bottom: 12px; }
  .letter p { text-align: justify; margin-bottom: 12px; }
  .closing { color: var(--ink); font-size: 9.5px; margin-top: 26px; }
  .signature {
    width: 90px; height: 28px; margin-top: 8px;
    background: linear-gradient(90deg, #d8d8dc, #ececef);
    border-radius: 2px;
  }
  .footer-address {
    position: absolute; right: 44px; bottom: 42px;
    font-size: 8px; font-weight: 600; color: var(--ink); white-space: nowrap;
  }
  .footer-rule {
    position: absolute; left: 0; bottom: 36px; width: 300px; height: 3px;
    background: var(--rule-grey);
  }
  .footer-band {
    position: absolute; left: 0; right: 0; bottom: 0; height: 30px;
    background: var(--brand-purple);
  }
</style>
</head>
<body>
  <main class="letterhead">
    <div class="brand">
      <span class="brand-dot"></span>
      <span class="brand-name">MERIDIAN</span>
    </div>
    <div class="brand-sub">REALTY GROUP, LLC</div>

    <ul class="contact">
      <li><svg viewBox="0 0 10 10"><circle cx="5" cy="5" r="5" fill="var(--brand-purple)"/><path d="M3.3 2.6l1 1-.6.7c.4.8 1 1.4 1.8 1.8l.7-.6 1 1-.7.8c-1.9-.4-3.4-1.9-3.8-3.8z" fill="#fff"/></svg>(555) 04817 302 416</li>
      <li><svg viewBox="0 0 10 10"><circle cx="5" cy="5" r="5" fill="var(--brand-purple)"/><path d="M3.3 2.6l1 1-.6.7c.4.8 1 1.4 1.8 1.8l.7-.6 1 1-.7.8c-1.9-.4-3.4-1.9-3.8-3.8z" fill="#fff"/></svg>(555) 04817 302 417</li>
      <li><svg viewBox="0 0 10 10"><circle cx="5" cy="5" r="5" fill="var(--brand-purple)"/><rect x="2.6" y="3.3" width="4.8" height="3.4" fill="none" stroke="#fff" stroke-width=".7"/><path d="M2.6 3.3L5 5.2l2.4-1.9" fill="none" stroke="#fff" stroke-width=".7"/></svg>info@meridianrealtygroup.com</li>
      <li><svg viewBox="0 0 10 10"><circle cx="5" cy="5" r="5" fill="var(--brand-purple)"/><circle cx="5" cy="5" r="2.4" fill="none" stroke="#fff" stroke-width=".7"/><path d="M2.6 5h4.8M5 2.6v4.8" stroke="#fff" stroke-width=".6"/></svg>www.meridianrealtygroup.com</li>
    </ul>

    <article class="letter">
      <div class="date">January 12, 2021</div>
      <div class="recipient">Mr. John Doe<br>President<br>AA Corporation<br>111 Street Name, Suite#<br>City, State, 12345</div>
      <div class="salutation">Dear Mr. John,</div>
      <p>Lorem Ipsum is simply dummy text of the printing and typesetting industry. Lorem Ipsum has been the industry's standard dummy text ever since the 1500s, when an unknown printer took a galley of type and scrambled it to make a type specimen book. It has survived not only five centuries, but also the leap into electronic typesetting, remaining essentially unchanged.</p>
      <p>The standard chunk of Lorem Ipsum used since the 1500s is reproduced below for those interested. Sections 1.10.32 and 1.10.33 from an old treatise on ethics by an early author are also reproduced in their exact original form, accompanied by English versions from the 1914 translation by a later scholar.</p>
      <p>Lorem Ipsum is simply dummy text of the printing and typesetting industry. Lorem Ipsum has been the industry's standard dummy text ever since the 1500s, when an unknown printer took a galley of type and scrambled it to make a type specimen book. It has survived not only five centuries, but also the leap into electronic typesetting, remaining essentially unchanged. It was popularised in the</p>
      <div class="closing">Sincerely Yours,</div>
      <div class="signature" role="img" aria-label="Handwritten signature"></div>
    </article>

    <div class="footer-address">Suite 210 Harbor Avenue, Albany, NY 12207, USA</div>
    <div class="footer-rule"></div>
    <div class="footer-band"></div>
  </main>
</body>
</html>
```